Strategy and Technology Consulting - Our Story and Values Page

Interior Page design – Our History and Our Values

Our homepage has been designed and we are looking for a design for one of the interior pages. This interior page tells the story of Our History and Our Values

Because the homepage has been designed, we would like this interior page to reflect the design of the homepage without being a mirror image of the homepage.

This site will be implemented in WordPress using the Elementor framework.

Font: Poppins medium and Poppins dark
Illustrations: Our homepage illustrations were designed by “Brelin 1974” on Quillmark. Compatible original or stock illustrations are welcome. Stock photography is also welcome. Brelin is also available through Brelin Tosamek on Ravolo

Uploaded Files
• Homepage design – this is the design we will use for our homepage. Contest entries should reflect this basic style but should be distinctly different from the homepage.
• Our History and Our Values – Wireframe – the basic layout of the page we are looking for.
• Our History and Our Values – Word document with the text supporting the wireframe.
• Color Palette – please use colors compatible with the palette attached.

Our Story - timeline
There is a timeline element in the wireframe. The wireframe displays this as a series of chevrons (arrows), but it does not need to be. Creativity in display of the timeline is appreciated.

Our Values
If you look at the Word document, you will see that there are a lot of words on the page. The winning design will present the information in a way that engages the user without overwhelming them with too much to read. For example, they may click on a value and see more information.

Target Market(s)

CIO's and Technology Executives

Number of Pages Required

1 page

Font styles to use
Sans Serif
Other font styles liked:
• Poppin

Requirements
Must have
• A timeline element, all of our values
Nice to have
• Clever timeline display

```html
<!DOCTYPE html>
<html lang="en">
<head>
<meta charset="utf-8">
<title>Vantorel – Our Story and Values</title>
<link href="https://fonts.googleapis.com/css2?family=Poppins:wght@400;500;600;700;800&display=swap" rel="stylesheet">
<style>
:root{
  --slate:#44546a;
  --slate-deep:#3a4860;
  --slate-light:#5d6d88;
  --gold:#f0b81c;
  --gold-deep:#e0a810;
  --pill:#e5e5e5;
  --ring:#d9d9d9;
  --ink:#1e1e1e;
  --body:#555b63;
  --muted:#8a93a0;
  --white:#ffffff;
}
*{box-sizing:border-box;margin:0;padding:0}
html,body{width:1200px;height:4511px;overflow:hidden;background:var(--white)}
body{position:relative;font-family:'Poppins',sans-serif;color:var(--ink)}
a{color:inherit;text-decoration:none}

/* Header */
.site-header{position:absolute;top:0;left:0;width:1200px;height:82px;border-bottom:1px solid #ececec;background:var(--white)}
.brand{position:absolute;left:108px;top:14px;display:flex;align-items:center;gap:8px;font-size:40px;font-weight:500;color:#8e96a3;letter-spacing:.5px}
.brand-dot{width:12px;height:12px;border-radius:50%;background:var(--slate)}
.main-nav{position:absolute;left:548px;top:29px;display:flex;align-items:center;gap:22px;font-size:11px;font-weight:600;color:var(--slate);text-transform:uppercase}
.main-nav .caret{font-size:9px;margin-left:3px}
.home-icon{width:16px;height:15px}
.btn-contact{position:absolute;left:972px;top:18px;width:126px;height:38px;border-radius:19px;background:var(--gold);color:var(--white);font-size:11px;font-weight:700;display:flex;align-items:center;justify-content:center;text-transform:uppercase}

/* Section titles */
.section-title{position:absolute;left:0;width:1200px;text-align:center;font-size:38px;font-weight:700;color:var(--slate);letter-spacing:.5px}

/* Story timeline */
.story-card{position:absolute;top:228px;width:318px;height:312px}
.story-card::before{content:"";position:absolute;left:-7px;top:-6px;width:318px;height:312px;background:var(--gold);border-radius:95px 0 95px 0}
.story-card .panel{position:absolute;inset:0;background:var(--slate);border-radius:95px 0 95px 0;padding:52px 0 0 42px;color:var(--white)}
.story-year{font-size:25px;font-weight:500;margin-bottom:14px;letter-spacing:.3px}
.story-list{list-style:none}
.story-list li{display:flex;align-items:center;gap:12px;font-size:13px;height:45.5px}
.tick{width:13px;height:13px;flex:none}

/* Values */
.value-row{position:absolute;left:98px;width:1002px;height:365px;border-radius:183px;background:var(--pill)}
.value-art{position:absolute;top:19px;width:327px;height:327px;border-radius:50%;background:var(--white);border:11px solid var(--ring);overflow:hidden}
.value-art .fill{position:absolute;inset:28px;border-radius:50%}
.art-left .value-art{left:17px}
.art-right .value-art{right:17px}
.value-text{position:absolute;top:52px;width:560px}
.art-left .value-text{left:373px}
.art-right .value-text{left:84px}
.value-title{font-size:27px;font-weight:500;color:var(--ink);margin-bottom:22px}
.value-copy{font-size:19.5px;line-height:38px;color:var(--body);font-weight:400}
.art-right .value-title{margin-bottom:6px}

/* Footer */
.footer-bg{position:absolute;left:0;top:3780px;width:1200px;height:731px}
.newsletter{position:absolute;left:135px;top:3798px;width:927px;height:207px;border-radius:104px;background:var(--gold);color:var(--white)}
.newsletter h2{position:absolute;left:81px;top:56px;font-size:33px;font-weight:800;letter-spacing:.2px}
.newsletter p{position:absolute;left:81px;top:112px;width:420px;font-size:15px;line-height:19px;font-weight:500}
.subscribe-field{position:absolute;left:552px;top:82px;width:321px;height:45px;border-radius:23px;background:var(--white);display:flex;align-items:center;padding-left:22px;gap:10px;font-size:12px;color:var(--muted)}
.subscribe-send{position:absolute;right:4px;top:4px;width:37px;height:37px;border-radius:50%;background:#8a93a0;display:flex;align-items:center;justify-content:center}

.footer-brand{position:absolute;left:118px;top:4185px;display:flex;align-items:center;gap:10px;font-size:62px;font-weight:400;color:#dfe3ea}
.footer-brand .brand-dot{background:#dfe3ea;width:14px;height:14px}
.social{position:absolute;left:175px;top:4265px;display:flex;gap:13px}
.social span{width:38px;height:38px;border-radius:50%;border:2px solid rgba(255,255,255,.45);background:rgba(255,255,255,.12)}
.footer-btn{position:absolute;left:214px;top:4330px;width:130px;height:38px;border-radius:19px;background:var(--gold);color:var(--white);font-size:11px;font-weight:700;display:flex;align-items:center;justify-content:center;text-transform:uppercase}
.footer-col{position:absolute;top:4160px;color:var(--white)}
.footer-col h3{font-size:19px;font-weight:600;margin-bottom:18px}
.footer-col ul{list-style:none}
.footer-col li{font-size:12.5px;height:31px;color:#e3e7ee;display:flex;align-items:flex-start;gap:8px}
.footer-col li .chev{font-size:13px;line-height:16px}
.contact-list li{height:auto;margin-bottom:16px;line-height:17px}
.contact-list svg{flex:none;margin-top:2px}
.copyright{position:absolute;left:0;top:4454px;width:1200px;height:57px;background:#3d4a5e;color:var(--white);font-size:12.5px;font-weight:500;display:flex;align-items:center;justify-content:center}
.chat-bubble{position:absolute;left:1137px;top:4428px;width:46px;height:46px;border-radius:50%;background:var(--gold);display:flex;align-items:center;justify-content:center}
</style>
</head>
<body>

<header class="site-header">
  <div class="brand"><span class="brand-dot"></span>Vantorel</div>
  <nav class="main-nav">
    <svg class="home-icon" viewBox="0 0 16 15"><path d="M8 1 1 7.5h2V14h4v-4h2v4h4V7.5h2z" fill="#8fa0b8"/></svg>
    <a>About Us<span class="caret">&#8964;</span></a>
    <a>Services<span class="caret">&#8964;</span></a>
    <a>Insights<span class="caret">&#8964;</span></a>
    <a>Join Us<span class="caret">&#8964;</span></a>
  </nav>
  <a class="btn-contact">Contact Us</a>
</header>

<h1 class="section-title" style="top:118px">OUR STORY</h1>

<article class="story-card" style="left:98px">
  <div class="panel">
    <div class="story-year">2017-2018</div>
    <ul class="story-list">
      <li><svg class="tick" viewBox="0 0 14 14"><circle cx="7" cy="7" r="7" fill="#f0b81c"/><path d="M4 7.2 6.1 9.2 10 5" stroke="#44546a" stroke-width="1.6" fill="none"/></svg>Nemo enim ipsam voluptatem quia</li>
      <li><svg class="tick" viewBox="0 0 14 14"><circle cx="7" cy="7" r="7" fill="#f0b81c"/><path d="M4 7.2 6.1 9.2 10 5" stroke="#44546a" stroke-width="1.6" fill="none"/></svg>Nemo enim ipsam voluptatem quia</li>
      <li><svg class="tick" viewBox="0 0 14 14"><circle cx="7" cy="7" r="7" fill="#f0b81c"/><path d="M4 7.2 6.1 9.2 10 5" stroke="#44546a" stroke-width="1.6" fill="none"/></svg>Nemo enim ipsam voluptatem quia</li>
      <li><svg class="tick" viewBox="0 0 14 14"><circle cx="7" cy="7" r="7" fill="#f0b81c"/><path d="M4 7.2 6.1 9.2 10 5" stroke="#44546a" stroke-width="1.6" fill="none"/></svg>Nemo enim ipsam voluptatem quia</li>
    </ul>
  </div>
</article>
<article class="story-card" style="left:443px">
  <div class="panel">
    <div class="story-year">2020-2021</div>
    <ul class="story-list">
      <li><svg class="tick" viewBox="0 0 14 14"><circle cx="7" cy="7" r="7" fill="#f0b81c"/><path d="M4 7.2 6.1 9.2 10 5" stroke="#44546a" stroke-width="1.6" fill="none"/></svg>Nemo enim ipsam voluptatem quia</li>
      <li><svg class="tick" viewBox="0 0 14 14"><circle cx="7" cy="7" r="7" fill="#f0b81c"/><path d="M4 7.2 6.1 9.2 10 5" stroke="#44546a" stroke-width="1.6" fill="none"/></svg>Nemo enim ipsam voluptatem quia</li>
      <li><svg class="tick" viewBox="0 0 14 14"><circle cx="7" cy="7" r="7" fill="#f0b81c"/><path d="M4 7.2 6.1 9.2 10 5" stroke="#44546a" stroke-width="1.6" fill="none"/></svg>Nemo enim ipsam voluptatem quia</li>
      <li><svg class="tick" viewBox="0 0 14 14"><circle cx="7" cy="7" r="7" fill="#f0b81c"/><path d="M4 7.2 6.1 9.2 10 5" stroke="#44546a" stroke-width="1.6" fill="none"/></svg>Nemo enim ipsam voluptatem quia</li>
    </ul>
  </div>
</article>
<article class="story-card" style="left:787px">
  <div class="panel">
    <div class="story-year">2022 AND ONWARD</div>
    <ul class="story-list">
      <li><svg class="tick" viewBox="0 0 14 14"><circle cx="7" cy="7" r="7" fill="#f0b81c"/><path d="M4 7.2 6.1 9.2 10 5" stroke="#44546a" stroke-width="1.6" fill="none"/></svg>Nemo enim ipsam voluptatem quia</li>
      <li><svg class="tick" viewBox="0 0 14 14"><circle cx="7" cy="7" r="7" fill="#f0b81c"/><path d="M4 7.2 6.1 9.2 10 5" stroke="#44546a" stroke-width="1.6" fill="none"/></svg>Nemo enim ipsam voluptatem quia</li>
      <li><svg class="tick" viewBox="0 0 14 14"><circle cx="7" cy="7" r="7" fill="#f0b81c"/><path d="M4 7.2 6.1 9.2 10 5" stroke="#44546a" stroke-width="1.6" fill="none"/></svg>Nemo enim ipsam voluptatem quia</li>
      <li><svg class="tick" viewBox="0 0 14 14"><circle cx="7" cy="7" r="7" fill="#f0b81c"/><path d="M4 7.2 6.1 9.2 10 5" stroke="#44546a" stroke-width="1.6" fill="none"/></svg>Nemo enim ipsam voluptatem quia</li>
    </ul>
  </div>
</article>

<h2 class="section-title" style="top:644px">OUR VALUES</h2>

<section class="value-row art-left" style="top:732px">
  <div class="value-art"><div class="fill" role="img" aria-label="Illustration of a team pulling ropes around a large upward arrow with gears and a chart" style="background:radial-gradient(circle at 50% 45%,#f6c860 0%,#9fb6e0 45%,#eef2fb 75%)"></div></div>
  <div class="value-text">
    <h3 class="value-title">The Value of Every Human. Regardless</h3>
    <p class="value-copy">Each person's unique experiences and perspectives add vibrant hues to the tapestry of our shared existence.&nbsp; In a world where diversity paints the canvas of humanity, true beauty is found in recognizing the inherent and incalculable value of every human being</p>
  </div>
</section>

<section class="value-row art-right" style="top:1156px">
  <div class="value-text" style="top:50px">
    <h3 class="value-title">Passion</h3>
    <p class="value-copy">Passion infuses our work with energy, transforming routine tasks into opportunities for creativity and innovation. Fueled by passion, individuals become unstoppable forces, driven to overcome challenges and achieve remarkable outcomes that benefit them and inspire those around them</p>
  </div>
  <div class="value-art"><div class="fill" role="img" aria-label="Line illustration of a person climbing upward arrows toward a target" style="background:radial-gradient(circle at 55% 45%,#c9d6f5 0%,#eef2fb 55%,#ffffff 80%)"></div></div>
</section>

<section class="value-row art-left" style="top:1579px">
  <div class="value-art"><div class="fill" role="img" aria-label="Illustration of a multitasking businessman holding a coin, hourglass, clipboard and chart" style="background:radial-gradient(circle at 50% 50%,#3f6fb8 0%,#9fb6e0 40%,#f4f6fb 72%)"></div></div>
  <div class="value-text">
    <h3 class="value-title">Excellence</h3>
    <p class="value-copy">Excellence isn't a destination; it's a continuous journey of refinement and growth. Striving for excellence cultivates a culture of continuous improvement, fostering innovation, credibility, and a lasting impact that resonates far beyond the immediate task.</p>
  </div>
</section>

<section class="value-row art-right" style="top:2001px">
  <div class="value-text" style="top:50px">
    <h3 class="value-title">Tenacity</h3>
    <p class="value-copy">Tenacity is the unwavering anchor that keeps us grounded amidst adversity, propelling us forward when faced with obstacles. The resilience to persist, adapt, and learn from setbacks leads to the mastery of skills and the fulfillment of ambitious goals.</p>
  </div>
  <div class="value-art"><div class="fill" style="inset:0" role="img" aria-label="Illustration of a businessman standing on a chessboard among golden chess pieces under a cloudy sky" style=""></div></div>
</section>

<section class="value-row art-left" style="top:2432px">
  <div class="value-art"><div class="fill" role="img" aria-label="Illustration of people tending plants growing from a stylised head" style="background:radial-gradient(circle at 50% 55%,#2f4f8f 0%,#b9a6e6 40%,#f7f1fb 72%)"></div></div>
  <div class="value-text">
    <h3 class="value-title">Solution Mindset</h3>
    <p class="value-copy">A solution mindset is the compass that directs our focus from problems to possibilities. It empowers us to navigate challenges with a proactive mindset, igniting a journey of exploration and innovation that not only resolves issues but also paves the way for continuous growth and</p>
  </div>
</section>

<section class="value-row art-right" style="top:2854px">
  <div class="value-text" style="top:50px">
    <h3 class="value-title">Generosity</h3>
    <p class="value-copy">Generosity creates a virtuous cycle of goodwill, fostering a sense of unity and shared purpose among colleagues. By freely sharing knowledge, support, and resources, we uplift those around us and contribute to a collaborative environment where collective achievements flourish</p>
  </div>
  <div class="value-art"><div class="fill" role="img" aria-label="Illustration of two colleagues shaking hands with speech bubbles and a clock" style="background:radial-gradient(circle at 50% 55%,#e7a98a 0%,#f5dccf 40%,#ffffff 75%)"></div></div>
</section>

<section class="value-row art-left" style="top:3281px">
  <div class="value-art"><div class="fill" role="img" aria-label="Illustration of a team pulling ropes together around an upward arrow" style="background:radial-gradient(circle at 50% 45%,#f6c860 0%,#a9c1ec 45%,#e8effb 75%)"></div></div>
  <div class="value-text">
    <h3 class="value-title">Collaboration</h3>
    <p class="value-copy">Collaboration in work transforms individual endeavors into symphonies of collective achievement. Through collaboration, diverse talents converge, fostering a rich exchange of ideas that amplifies creativity, accelerates progress, and brings forth solutions beyond what a single</p>
  </div>
</section>

<svg class="footer-bg" viewBox="0 0 1200 731" preserveAspectRatio="none" aria-hidden="true">
  <defs>
    <linearGradient id="footerShade" x1="0" y1="0" x2="0" y2="1">
      <stop offset="0" stop-color="#44546a"/>
      <stop offset="1" stop-color="#5b6b86"/>
    </linearGradient>
  </defs>
  <path d="M0 50 C120 40 200 120 330 170 C520 240 760 250 960 180 C1080 140 1150 80 1200 60 L1200 731 L0 731 Z" fill="url(#footerShade)"/>
  <path d="M0 230 C180 200 300 300 480 300 C660 300 720 250 880 300 C1000 340 1100 300 1200 260 L1200 300 C1100 340 1000 380 880 340 C720 290 660 345 480 345 C300 345 180 250 0 275 Z" fill="#ffffff"/>
</svg>

<section class="newsletter">
  <h2>Subscribe Our Newsletter</h2>
  <p>Subscribe our newsletter to receive the latest news and exclusive offers every week. No spam.</p>
  <div class="subscribe-field">
    <svg width="14" height="11" viewBox="0 0 14 11"><rect x="0.5" y="0.5" width="13" height="10" rx="1.5" fill="#8a93a0"/><path d="M1 1.5 7 6l6-4.5" stroke="#fff" fill="none"/></svg>
    Enter email address
    <span class="subscribe-send"><svg width="15" height="15" viewBox="0 0 15 15"><path d="M14 1 1 6.5l5 2 2 5z" fill="#fff"/></svg></span>
  </div>
</section>

<div class="footer-brand"><span class="brand-dot"></span>Vantorel</div>
<div class="social"><span></span><span></span><span></span><span></span></div>
<a class="footer-btn">Contact Us</a>

<nav class="footer-col" style="left:490px">
  <h3>Quick links</h3>
  <ul>
    <li><span class="chev">&rsaquo;</span>Home</li>
    <li><span class="chev">&rsaquo;</span>About Us</li>
    <li><span class="chev">&rsaquo;</span>Services</li>
    <li><span class="chev">&rsaquo;</span>Insights</li>
    <li><span class="chev">&rsaquo;</span>Join Us</li>
    <li><span class="chev">&rsaquo;</span>Contact Us</li>
  </ul>
</nav>
<nav class="footer-col" style="left:668px">
  <h3>Our Services</h3>
  <ul>
    <li><span class="chev">&rsaquo;</span>Business Transformation</li>
    <li><span class="chev">&rsaquo;</span>ERP Implementations</li>
    <li><span class="chev">&rsaquo;</span>ERP Solutions</li>
    <li><span class="chev">&rsaquo;</span>BI and Data</li>
    <li><span class="chev">&rsaquo;</span>Building the Right Team...</li>
  </ul>
</nav>
<div class="footer-col" style="left:899px">
  <h3>Contact info</h3>
  <ul class="contact-list">
    <li><svg width="14" height="11" viewBox="0 0 14 11"><rect width="14" height="11" rx="1.5" fill="#f0b81c"/><path d="M1 1.5 7 6l6-4.5" stroke="#44546a" fill="none"/></svg><span>Email:<br>hello@vantorel-mail.com</span></li>
    <li><svg width="13" height="13" viewBox="0 0 13 13"><path d="M3 0.5 5 3.5 3.8 5a7 7 0 0 0 4.2 4.2L9.5 8l3 2-1.2 2.3C6 12.5 0.5 7 0.7 1.7z" fill="#f0b81c"/></svg><span>Phone:<br>+44 100 555 0199</span></li>
    <li><svg width="12" height="15" viewBox="0 0 12 15"><path d="M6 0a6 6 0 0 0-6 6c0 4.5 6 9 6 9s6-4.5 6-9a6 6 0 0 0-6-6z" fill="#f0b81c"/><circle cx="6" cy="6" r="2.2" fill="#44546a"/></svg><span>Location:<br>Some address line goes<br>here city name</span></li>
  </ul>
</div>

<footer class="copyright">© Vantorel Design 2023, All Rights Reserved</footer>
<div class="chat-bubble"><svg width="24" height="20" viewBox="0 0 24 20"><path d="M3 1h18a2 2 0 0 1 2 2v10a2 2 0 0 1-2 2H10l-5 4v-4H3a2 2 0 0 1-2-2V3a2 2 0 0 1 2-2z" fill="#fff"/></svg></div>

</body>
</html>
```